Harrow Grading LLC business card design

Excavation company business cards

Contact Information for Business Card

Harrow Grading LLC cell phone 208-417-6290 office phone 208-319-4856 harrowgradingllc@maplecove.com Driveways, site prep, retaining walls, septic systems, rock delivery

Colors

Designer to choose colors to be used in the design.

```html
<!DOCTYPE html>
<html lang="en">
<head>
<meta charset="utf-8">
<title>Harrow Grading LLC — Business Card</title>
<link rel="stylesheet" href="https://fonts.googleapis.com/css2?family=Roboto:ital,wght@0,400;0,700;0,900;1,400&display=swap">
<style>
  :root {
    --stage: #2a2a2c;
    --card: #1c1c1d;
    --card-edge: #252527;
    --orange: #f07022;
    --white: #f4f4f4;
    --muted: #cfcfcf;
    --pattern-dark: #232325;
    --pattern-light: #4a4a4d;
  }
  * { box-sizing: border-box; margin: 0; padding: 0; }
  html, body { width: 1200px; height: 900px; overflow: hidden; }
  body {
    background: var(--stage);
    font-family: "Roboto", sans-serif;
    color: var(--white);
    display: flex;
    flex-direction: column;
    align-items: center;
    justify-content: center;
    gap: 56px;
  }
  .card {
    position: relative;
    width: 630px;
    height: 360px;
    border-radius: 22px;
    background: var(--card);
    overflow: hidden;
    box-shadow: 0 14px 34px rgba(0,0,0,.45);
  }

  /* Front */
  .card-front::after {
    content: "";
    position: absolute;
    left: 0; right: 0; bottom: 0;
    height: 16px;
    background: var(--orange);
  }
  .brand {
    position: absolute;
    left: 48px; top: 120px;
    width: 250px;
    display: flex;
    align-items: center;
    gap: 14px;
  }
  .brand-mark {
    width: 18px; height: 18px;
    border-radius: 50%;
    background: var(--orange);
    flex: none;
  }
  .brand-name {
    font-weight: 900;
    font-size: 30px;
    line-height: 1.05;
    text-transform: uppercase;
    color: var(--orange);
    letter-spacing: .5px;
  }
  .divider {
    position: absolute;
    left: 318px; top: 78px;
    width: 1.5px; height: 190px;
    background: var(--orange);
    opacity: .8;
  }
  .contact {
    position: absolute;
    left: 346px; top: 84px;
  }
  .person-name {
    font-weight: 900;
    font-size: 26px;
    color: var(--orange);
    text-transform: uppercase;
    letter-spacing: .5px;
  }
  .person-role {
    font-style: italic;
    font-size: 17px;
    margin-bottom: 22px;
  }
  .contact-list { list-style: none; }
  .contact-list li {
    display: flex;
    align-items: center;
    gap: 9px;
    font-size: 15px;
    line-height: 26px;
  }
  .contact-list svg { width: 14px; height: 14px; fill: var(--orange); flex: none; }

  /* Back */
  .back-pattern {
    position: absolute; inset: 0;
    background:
      radial-gradient(ellipse at 75% 40%, var(--pattern-light) 0%, transparent 55%),
      linear-gradient(135deg, var(--pattern-dark) 0%, #2e2e31 55%, var(--pattern-light) 100%);
  }
  .back-brand {
    position: absolute;
    left: 50%; top: 110px;
    transform: translateX(-50%);
    display: flex; align-items: center; gap: 12px;
    white-space: nowrap;
  }
  .back-brand .brand-name { font-size: 28px; }
  .services {
    position: absolute;
    left: 48px; bottom: 48px;
    list-style: none;
    display: grid;
    grid-template-columns: repeat(3, auto);
    column-gap: 26px;
    row-gap: 8px;
    font-size: 19px;
  }
  .services li::before {
    content: "•";
    color: var(--orange);
    margin-right: 5px;
  }
</style>
</head>
<body>

  <section class="card card-front" aria-label="Business card front">
    <div class="brand">
      <span class="brand-mark"></span>
      <span class="brand-name">Harrow Grading LLC</span>
    </div>
    <div class="divider"></div>
    <div class="contact">
      <h1 class="person-name">Dalton Reyes</h1>
      <p class="person-role">Founder</p>
      <ul class="contact-list">
        <li>
          <svg viewBox="0 0 24 24"><path d="M6.6 10.8a15.1 15.1 0 0 0 6.6 6.6l2.2-2.2a1 1 0 0 1 1-.25 11.4 11.4 0 0 0 3.6.57 1 1 0 0 1 1 1V20a1 1 0 0 1-1 1A17 17 0 0 1 3 4a1 1 0 0 1 1-1h3.5a1 1 0 0 1 1 1c0 1.25.2 2.45.57 3.57a1 1 0 0 1-.25 1z"/></svg>
          208-319-4856
        </li>
        <li>
          <svg viewBox="0 0 24 24"><path d="M7 1h10a2 2 0 0 1 2 2v18a2 2 0 0 1-2 2H7a2 2 0 0 1-2-2V3a2 2 0 0 1 2-2zm0 3v14h10V4zm5 15.5a1 1 0 1 0 0 2 1 1 0 0 0 0-2z"/></svg>
          208-417-6290
        </li>
        <li>
          <svg viewBox="0 0 24 24"><path d="M2 5h20v14H2zm2 2v.5l8 5 8-5V7zm0 2.8V17h16V9.8l-8 5z"/></svg>
          harrowgradingllc@maplecove.com
        </li>
        <li>
          <svg viewBox="0 0 24 24"><path d="M12 2a10 10 0 1 0 0 20 10 10 0 0 0 0-20zm6.9 6h-2.9a15 15 0 0 0-1.4-3.6A8 8 0 0 1 18.9 8zM12 4a13 13 0 0 1 1.9 4h-3.8A13 13 0 0 1 12 4zM4.3 14a8 8 0 0 1 0-4h3.4a16 16 0 0 0 0 4zm.8 2h2.9a15 15 0 0 0 1.4 3.6A8 8 0 0 1 5.1 16zM8 8H5.1a8 8 0 0 1 4.3-3.6A15 15 0 0 0 8 8zm4 12a13 13 0 0 1-1.9-4h3.8A13 13 0 0 1 12 20zm2.3-6H9.7a14 14 0 0 1 0-4h4.6a14 14 0 0 1 0 4zm.3 5.6A15 15 0 0 0 16 16h2.9a8 8 0 0 1-4.3 3.6zM16.3 14a16 16 0 0 0 0-4h3.4a8 8 0 0 1 0 4z"/></svg>
          www.harrowgradingllc.com
        </li>
      </ul>
    </div>
  </section>

  <section class="card card-back" aria-label="Business card back">
    <div class="back-pattern" role="img" aria-label="Repeating pattern of excavator and mountain silhouettes in graded greys"></div>
    <div class="back-brand">
      <span class="brand-mark"></span>
      <span class="brand-name">Harrow Grading LLC</span>
    </div>
    <ul class="services">
      <li>Driveways</li>
      <li>Retaining Walls</li>
      <li></li>
      <li>Site Prep</li>
      <li>Septic Systems</li>
      <li>Rock Delivery</li>
    </ul>
  </section>

</body>
</html>
```